life insurance quote website design for lepontdoriole.ca

the web site lepontdoriole.ca need a design. we dont like the actuel one but we are open at all new suggestion. visit us at lepontdoriole.ca and you will understand. the principal concurant is tarifsgarantisnord.ca, calculeo.ca, coutprotecfam.ca. We are a life insurance quote site. we found best price available in the canadien industrie. We absolutly want a design with our form in the front page on the top right side like our concurance, we use wordpress at this time. we want to be able to switch language. and to have a logic form. we want to be able to change the color for each type of insurance quote page.we also need a blog in it to post news. and the site will be SEO accurate.

Target Market(s)

Get client fill the quote form

Industry/Entity Type

Insurance

Number of Pages Required

3 page

Font styles to use
Sans Serif

Requirements
Must have
• logic form on the top right first page
• page template for product info stuff, contact, and who we are, blog
• French site
• custum color
Nice to have
• Wordpress design will be appréciate
• switch language english/french

```html
<!DOCTYPE html>
<html lang="en">
<head>
<meta charset="utf-8">
<title>Le Pont d'Oriole – Life Insurance Quotes</title>
<link rel="stylesheet" href="https://fonts.googleapis.com/css2?family=Open+Sans:wght@400;600;700;800&family=Arimo:wght@400;700&display=swap">
<style>
:root{
  --red:#e31b1f;
  --navy:#173a6b;
  --blue:#2456a0;
  --panel:#1f4c91;
  --ink:#1c1c1c;
  --text:#666;
  --grey-bg:#f2f2f2;
  --footer:#262626;
  --footer-bottom:#1d1d1d;
  --cyan:#2ab4d8;
  --gold:#d6a445;
  --green:#79bf44;
  --pink:#e8637f;
  --white:#fff;
}
*{box-sizing:border-box;margin:0;padding:0}
html,body{width:1200px;height:2446px;overflow:hidden}
body{position:relative;background:var(--white);font-family:"Open Sans",Arial,sans-serif;color:var(--text)}
.abs{position:absolute}
.head-font{font-family:"Arimo",Arial,sans-serif}

/* header */
.topline{left:0;top:0;width:1200px;height:5px;background:var(--red)}
.brand{left:82px;top:40px;display:flex;align-items:center;gap:10px;z-index:3}
.brand-square{width:22px;height:22px;background:var(--red)}
.brand-name{font-weight:700;font-size:20px;color:var(--red);background:var(--white);padding:4px 8px}
.toplinks{left:548px;top:20px;display:flex;align-items:center;font-size:12px;color:#333;gap:8px}
.flag{width:18px;height:12px;display:inline-block;vertical-align:-1px;margin-right:4px}
.flag-en{background:linear-gradient(#1d3f85,#1d3f85)}
.flag-fr{background:linear-gradient(90deg,#1d3f85 33%,#fff 33% 66%,#d2232a 66%)}
.round-icon{width:30px;height:30px;border-radius:50%;background:var(--red);display:inline-flex;align-items:center;justify-content:center;margin:0 6px 0 14px}
.toplinks .contact-text{font-size:13px}
.nav{left:556px;top:64px;display:flex;gap:34px;font-size:12.5px;font-weight:700;color:#222}
.nav .active{color:var(--red)}

/* hero */
.hero{left:0;top:93px;width:1200px;height:469px;background:linear-gradient(180deg,#cfe0ee 0%,#e9eef0 38%,#b8c88a 62%,#7f9d3f 100%)}
.hero-title{left:98px;top:290px;color:#fff;text-shadow:0 2px 4px rgba(0,0,0,.55);font-family:"Arimo",Arial,sans-serif}
.hero-title .small{font-size:27px;display:block;letter-spacing:.5px}
.hero-title .big{font-size:41px;font-weight:700;display:block;margin-top:2px}
.hero-arrow{top:306px}
.quote{left:699px;top:93px;width:401px;height:469px;background:rgba(31,76,145,.95);color:#fff}
.quote h2{text-align:center;font-size:21px;font-weight:700;margin-top:8px}
.q-group{position:absolute;left:23px;font-size:13.5px;font-weight:700}
.q-rule{position:absolute;left:120px;width:255px;height:1px;background:rgba(255,255,255,.6)}
.q-label{position:absolute;left:23px;font-size:12px}
.q-input{position:absolute;left:152px;width:225px;height:31px;background:#fff}
.q-select::after{content:"";position:absolute;right:0;top:0;width:32px;height:31px;background:#e6e6e6}
.q-check{display:inline-block;width:14px;height:14px;background:#fff;vertical-align:-2px;margin-right:8px}
.q-send{position:absolute;left:23px;top:419px;width:359px;height:37px;background:var(--red);color:#fff;font-weight:700;text-align:center;line-height:37px;font-size:14px}

/* welcome */
.sec-title{font-family:"Arimo",Arial,sans-serif;font-weight:700;color:var(--ink)}
.sec-title span{color:var(--blue)}
.welcome-title{left:0;top:598px;width:1200px;text-align:center;font-size:23px}
.welcome-lead{left:195px;top:645px;width:810px;text-align:center;font-size:12px;line-height:24px}
.feature{top:717px;width:240px;text-align:center}
.feature svg{display:block;margin:0 auto}
.feature h3{font-family:"Arimo",Arial,sans-serif;font-size:15.5px;color:var(--ink);margin-top:22px}
.feature p{font-size:12px;line-height:23px;margin-top:10px}
.feature .link{font-size:12px;font-weight:700;color:var(--red);margin-top:7px;display:block}

/* submission */
.submission{left:0;top:1024px;width:1200px;height:410px;background:var(--grey-bg)}
.sub-title{left:98px;top:1066px;font-size:21px}
.sub-sub{left:98px;top:1114px;font-size:18.5px;font-weight:600;color:#333}
.sub-text{left:98px;top:1155px;width:505px;font-size:12px;line-height:23px}
.sub-list{left:98px;top:1237px;list-style:none;font-size:12px}
.sub-list li{height:35px;display:flex;align-items:flex-start;gap:12px}
.sub-more{left:98px;top:1378px;font-size:12px;font-weight:700;color:var(--red)}
.sub-photo{left:632px;top:1073px;width:468px;height:309px;border:5px solid #fff;box-shadow:0 0 3px rgba(0,0,0,.2);background:linear-gradient(135deg,#c9b8a6,#e8ddd2 45%,#9fb3c9)}

/* blog */
.blog-title{left:0;top:1477px;width:1200px;text-align:center;font-size:23px}
.card{top:1529px;width:236px}
.card-img{position:relative;width:236px;height:147px;border:3px solid #fff;box-shadow:0 0 3px rgba(0,0,0,.25)}
.card-date{position:absolute;right:0;bottom:0;background:rgba(20,20,20,.85);color:#fff;font-size:11px;font-weight:700;padding:3px 7px}
.card h4{font-family:"Arimo",Arial,sans-serif;font-size:14px;color:var(--ink);line-height:21px;margin-top:18px;min-height:21px}
.card p{font-size:12px;line-height:23px;margin-top:5px}
.card .link{position:absolute;top:280px;font-size:11.5px;font-weight:700;color:var(--red)}

/* offices */
.offices{left:0;top:1858px;width:1200px;height:282px;background:linear-gradient(180deg,#5ea6dc 0%,#bfdcf1 55%,#9ac76a 85%,#6a9a34 100%)}
.offices-photo{left:740px;top:1880px;width:460px;height:260px;background:linear-gradient(135deg,rgba(230,200,170,.85),rgba(190,150,120,.85))}
.off-title{left:101px;top:1896px;font-size:21px}
.off-list{font-size:12.5px;font-weight:600;color:#111;list-style:none}
.off-list li{height:36px;display:flex;align-items:flex-start;gap:12px}

/* footer */
.footer{left:0;top:2140px;width:1200px;height:240px;background:var(--footer);color:#ddd}
.footer-brand{left:88px;top:2242px;display:flex;align-items:center;gap:8px}
.footer-brand .brand-name{font-size:16px;background:none;padding:0}
.divider{top:2170px;width:1px;height:182px;background:#3a3a3a}
.f-head{font-family:"Arimo",Arial,sans-serif;font-size:15px;font-weight:700;color:#fff}
.f-text{font-size:12px;color:#ddd;line-height:22px}
.hours td{padding:0 0 16px 0;font-size:12px}
.news-input{left:541px;top:2261px;width:262px;height:34px;background:#fff;font-size:11px;color:#888;padding:9px 13px}
.news-btn{left:541px;top:2309px;border:2px solid #fff;color:#fff;font-weight:700;font-size:12px;padding:7px 11px;border-radius:2px}
.contact-row{display:flex;align-items:center;gap:16px;font-size:12px}
.bottom{left:0;top:2380px;width:1200px;height:66px;background:var(--footer-bottom)}
.copy{left:99px;top:2400px;font-size:11.5px;color:#ccc}
.social{left:970px;top:2394px;display:flex;gap:8px}
.social span{width:28px;height:28px;border:2px solid #fff;border-radius:50%}
</style>
</head>
<body>

<!-- header -->
<div class="abs topline"></div>
<div class="abs brand"><span class="brand-square"></span><span class="brand-name">Le Pont d'Oriole</span></div>
<div class="abs toplinks">
  <span><i class="flag flag-en"></i>English</span>
  <span style="margin-left:10px"><i class="flag flag-fr"></i>French</span>
  <span class="round-icon"><svg width="14" height="11" viewBox="0 0 14 11"><rect x="0.5" y="0.5" width="13" height="10" fill="none" stroke="#fff"/><path d="M1 1l6 5 6-5" fill="none" stroke="#fff"/></svg></span>
  <span class="contact-text">contact@lepontdoriole.ca</span>
  <span class="round-icon" style="margin-left:22px"><svg width="14" height="14" viewBox="0 0 24 24"><path d="M6.6 10.8a15 15 0 006.6 6.6l2.2-2.2c.3-.3.7-.4 1-.2 1.1.4 2.3.6 3.6.6.6 0 1 .4 1 1V20c0 .6-.4 1-1 1A17 17 0 013 4c0-.6.4-1 1-1h3.5c.6 0 1 .4 1 1 0 1.3.2 2.5.6 3.6.1.3 0 .7-.2 1z" fill="#fff"/></svg></span>
  <span class="contact-text">1-855-555-0147</span>
</div>
<nav class="abs nav">
  <span class="active">HOME</span><span>PRODUCTS</span><span>SUBMISSION</span><span>WHO ARE WE?</span><span>CONTACT US</span>
  <svg width="12" height="12" viewBox="0 0 12 12"><circle cx="5" cy="5" r="3.8" fill="none" stroke="#222" stroke-width="1.8"/><path d="M8 8l3.2 3.2" stroke="#222" stroke-width="2"/></svg>
</nav>

<!-- hero -->
<div class="abs hero" role="img" aria-label="Photo of a smiling family in a sunny meadow, father carrying a child on his shoulders"></div>
<div class="abs hero-title"><span class="small">THE ASSURANCE OF</span><span class="big">GETTING THE BEST PRICE</span></div>
<svg class="abs hero-arrow" style="left:50px" width="16" height="30" viewBox="0 0 16 30"><path d="M14 2L2 15l12 13" fill="none" stroke="#fff" stroke-width="3"/></svg>
<svg class="abs hero-arrow" style="left:1148px" width="16" height="30" viewBox="0 0 16 30"><path d="M2 2l12 13L2 28" fill="none" stroke="#fff" stroke-width="3"/></svg>

<form class="abs quote">
  <h2 class="head-font">QUOTE REQUEST</h2>
  <div class="q-group" style="top:52px">Product</div><div class="q-rule" style="top:62px;left:82px;width:293px"></div>
  <div class="q-label" style="top:78px">Type of Insurance &nbsp;:</div><div class="q-input q-select" style="top:71px"></div>
  <div class="q-group" style="top:112px">Applicant</div><div class="q-rule" style="top:122px;left:94px;width:281px"></div>
  <div class="q-label" style="top:144px">Full Name * &nbsp;:</div><div class="q-input" style="top:136px"></div>
  <div class="q-label" style="top:180px">Cities * &nbsp;:</div><div class="q-input" style="top:172px"></div>
  <div class="q-label" style="top:216px">Email * &nbsp;:</div><div class="q-input" style="top:208px"></div>
  <div class="q-label" style="top:252px">Phone * &nbsp;:</div><div class="q-input" style="top:244px"></div>
  <div class="q-label" style="top:288px">Age * &nbsp;:</div><div class="q-input" style="top:280px"></div>
  <div class="q-label" style="top:320px">Gender * &nbsp;:</div>
  <div class="q-label" style="top:320px;left:152px"><i class="q-check"></i>Man &nbsp;&nbsp;&nbsp;&nbsp;&nbsp;<i class="q-check"></i>Wife</div>
  <div class="q-group" style="top:345px">Co-Applicant</div><div class="q-rule" style="top:355px;left:120px"></div>
  <div class="q-label" style="top:376px"><i class="q-check"></i>Add a co-applicant</div>
  <div class="q-label" style="top:376px;left:175px;width:210px;line-height:16px;padding-left:22px;text-indent:-22px"><i class="q-check"></i>I have read and accept the use and privacy policy of **</div>
  <div class="q-send">SEND</div>
</form>

<!-- welcome -->
<h1 class="abs sec-title welcome-title">WELCOME TO <span>LE PONT D'ORIOLE</span></h1>
<p class="abs welcome-lead">Our mission is to help our customers find the insurance that best meets their needs taking into account the best possible price. The consultant team always realize the financial needs analysis to determine the best choice of product.</p>

<div class="abs feature" style="left:84px">
  <svg width="110" height="130" viewBox="0 0 110 130"><path d="M8 14Q55 -2 102 14V70Q100 108 55 126Q10 108 8 70Z" fill="none" stroke="var(--cyan)" stroke-width="4"/>
    <circle cx="45" cy="58" r="9" fill="var(--cyan)"/><path d="M28 88q17-22 34 0z" fill="var(--cyan)"/><rect x="56" y="34" width="28" height="18" rx="3" fill="none" stroke="var(--cyan)" stroke-width="3"/></svg>
  <h3>ASSURANCE VIE</h3>
  <p>A fast, free and confidential. Fill the life insurance quote form and you will enjoy your experience with us</p>
  <span class="link">BIDDING</span>
</div>
<div class="abs feature" style="left:348px">
  <svg width="110" height="130" viewBox="0 0 110 130"><path d="M8 14Q55 -2 102 14V70Q100 108 55 126Q10 108 8 70Z" fill="none" stroke="var(--gold)" stroke-width="4"/>
    <rect x="44" y="30" width="28" height="20" fill="none" stroke="var(--gold)" stroke-width="3"/><path d="M30 60h30q8 0 8 8v14q0 8-8 8H38q-8 0-8-8z" fill="var(--gold)"/></svg>
  <h3>SALAIRE</h3>
  <p>A fast, free and confidential. Fill the life insurance quote form and you will enjoy your experience with us</p>
  <span class="link">BIDDING</span>
</div>
<div class="abs feature" style="left:609px">
  <svg width="110" height="130" viewBox="0 0 110 130"><path d="M8 14Q55 -2 102 14V70Q100 108 55 126Q10 108 8 70Z" fill="none" stroke="var(--green)" stroke-width="4"/>
    <rect x="36" y="30" width="36" height="50" rx="2" fill="none" stroke="var(--green)" stroke-width="3"/><path d="M44 44h20M44 54h20M44 64h12" stroke="var(--green)" stroke-width="3"/><circle cx="70" cy="78" r="10" fill="#fff" stroke="var(--green)" stroke-width="3"/><path d="M65 78l4 4 6-7" fill="none" stroke="var(--green)" stroke-width="3"/></svg>
  <h3>HYPOTHECAIRE</h3>
  <p>A fast, free and confidential. Fill the life insurance quote form and you will enjoy your experience with us</p>
  <span class="link">BIDDING</span>
</div>
<div class="abs feature" style="left:871px">
  <svg width="110" height="130" viewBox="0 0 110 130"><path d="M8 14Q55 -2 102 14V70Q100 108 55 126Q10 108 8 70Z" fill="none" stroke="var(--pink)" stroke-width="4"/>
    <path d="M55 88L30 62Q22 50 32 40Q44 32 55 46Q66 32 78 40Q88 50 80 62Z" fill="var(--pink)"/><path d="M30 60h12l5-8 6 16 5-10h20" fill="none" stroke="#fff" stroke-width="3"/></svg>
  <h3>MALADIES GRAVES</h3>
  <p>A fast, free and confidential. Fill the life insurance quote form and you will enjoy your experience with us</p>
  <span class="link">BIDDING</span>
</div>

<!-- submission -->
<div class="abs submission"></div>
<h2 class="abs sec-title sub-title">ONLINE <span>LIFE INSURANCE SUBMISSION</span></h2>
<div class="abs sub-sub">Find the Best Insurance at the Best Price!</div>
<p class="abs sub-text">Whether you are looking for life insurance, mortgage insurance or else you certainly want to pay the most advantageous price. Navigating among the many offers in the field of insurance can be a real headache.</p>
<ul class="abs sub-list">
  <li><svg width="14" height="14" viewBox="0 0 14 14"><circle cx="7" cy="7" r="7" fill="var(--red)"/><path d="M3.5 7l2.5 2.5 4.5-5" fill="none" stroke="#fff" stroke-width="2"/></svg>Permanent life insurance - term life insurance</li>
  <li><svg width="14" height="14" viewBox="0 0 14 14"><circle cx="7" cy="7" r="7" fill="var(--red)"/><path d="M3.5 7l2.5 2.5 4.5-5" fill="none" stroke="#fff" stroke-width="2"/></svg>Disability Insurance - Disability insurance</li>
  <li><svg width="14" height="14" viewBox="0 0 14 14"><circle cx="7" cy="7" r="7" fill="var(--red)"/><path d="M3.5 7l2.5 2.5 4.5-5" fill="none" stroke="#fff" stroke-width="2"/></svg>Mortgage Insurance - loans</li>
  <li><svg width="14" height="14" viewBox="0 0 14 14"><circle cx="7" cy="7" r="7" fill="var(--red)"/><path d="M3.5 7l2.5 2.5 4.5-5" fill="none" stroke="#fff" stroke-width="2"/></svg>Critical illness insurance</li>
</ul>
<span class="abs sub-more">READ MORE &gt;&gt;</span>
<div class="abs sub-photo" role="img" aria-label="Photo of a smiling team of insurance advisors"></div>

<!-- blog -->
<h2 class="abs sec-title blog-title">OUR <span>BLOG</span></h2>
<article class="abs card" style="left:98px">
  <div class="card-img" role="img" aria-label="Photo of an advisor meeting a couple at a table" style="background:linear-gradient(135deg,#a9b7c6,#e2d4c4)"><span class="card-date">05/04/2016</span></div>
  <h4>HOW TO PROCEED?</h4>
  <p>Simply fill in the insurance quote online form above, clicking on the insurance category that fits your needs.</p>
  <span class="link">READ MORE &gt;&gt;</span>
</article>
<article class="abs card" style="left:354px">
  <div class="card-img" role="img" aria-label="Photo of a financial advisor with a family" style="background:linear-gradient(135deg,#c7b19c,#e8e2da)"><span class="card-date">05/04/2016</span></div>
  <h4>COMPETENT FINANCIAL<br>ADVISORS SECURITY</h4>
  <p>Team Le Pont d'Oriole offers an innovative service in the field,...</p>
  <span class="link">READ MORE &gt;&gt;</span>
</article>
<article class="abs card" style="left:608px">
  <div class="card-img" role="img" aria-label="Photo of a senior couple meeting an advisor" style="background:linear-gradient(135deg,#b58a6a,#ddd0c2)"><span class="card-date">05/04/2016</span></div>
  <h4>THE IMPORTANCE OF<br>NOT OVERPAYING</h4>
  <p>Disbursing monthly or annually money for insurance is a considerable expense.</p>
  <span class="link">READ MORE &gt;&gt;</span>
</article>
<article class="abs card" style="left:864px">
  <div class="card-img" role="img" aria-label="Illustration about saving money, businessman on a blue background" style="background:linear-gradient(135deg,#1f8fd0,#7ec3ea)"><span class="card-date">05/04/2016</span></div>
  <h4>INSURANCE: ? HOW TO FIND</h4>
  <p>The life insurance market premium may seem complex at first. Indeed, insurers offer a variety of products ..</p>
  <span class="link">READ MORE &gt;&gt;</span>
</article>

<!-- offices -->
<div class="abs offices" role="img" aria-label="Blue sky over a green field"></div>
<div class="abs offices-photo" role="img" aria-label="Photo of a happy family lying in the grass"></div>
<h2 class="abs sec-title off-title">OUR <span>OFFICES</span></h2>
<ul class="abs off-list" style="left:101px;top:1949px">
  <li><svg width="14" height="14" viewBox="0 0 14 14"><circle cx="7" cy="7" r="7" fill="var(--red)"/><path d="M3.5 7l2.5 2.5 4.5-5" fill="none" stroke="#fff" stroke-width="2"/></svg>MONTREAL</li>
  <li><svg width="14" height="14" viewBox="0 0 14 14"><circle cx="7" cy="7" r="7" fill="var(--red)"/><path d="M3.5 7l2.5 2.5 4.5-5" fill="none" stroke="#fff" stroke-width="2"/></svg>QUEBEC</li>
  <li><svg width="14" height="14" viewBox="0 0 14 14"><circle cx="7" cy="7" r="7" fill="var(--red)"/><path d="M3.5 7l2.5 2.5 4.5-5" fill="none" stroke="#fff" stroke-width="2"/></svg>SHERBROOKE</li>
  <li><svg width="14" height="14" viewBox="0 0 14 14"><circle cx="7" cy="7" r="7" fill="var(--red)"/><path d="M3.5 7l2.5 2.5 4.5-5" fill="none" stroke="#fff" stroke-width="2"/></svg>GRANBY</li>
  <li><svg width="14" height="14" viewBox="0 0 14 14"><circle cx="7" cy="7" r="7" fill="var(--red)"/><path d="M3.5 7l2.5 2.5 4.5-5" fill="none" stroke="#fff" stroke-width="2"/></svg>BEAUCE</li>
</ul>
<ul class="abs off-list" style="left:240px;top:1949px">
  <li><svg width="14" height="14" viewBox="0 0 14 14"><circle cx="7" cy="7" r="7" fill="var(--red)"/><path d="M3.5 7l2.5 2.5 4.5-5" fill="none" stroke="#fff" stroke-width="2"/></svg>THREE RIVÈRES</li>
  <li><svg width="14" height="14" viewBox="0 0 14 14"><circle cx="7" cy="7" r="7" fill="var(--red)"/><path d="M3.5 7l2.5 2.5 4.5-5" fill="none" stroke="#fff" stroke-width="2"/></svg>PIEDMONT</li>
  <li><svg width="14" height="14" viewBox="0 0 14 14"><circle cx="7" cy="7" r="7" fill="var(--red)"/><path d="M3.5 7l2.5 2.5 4.5-5" fill="none" stroke="#fff" stroke-width="2"/></svg>SAGUENAY</li>
  <li><svg width="14" height="14" viewBox="0 0 14 14"><circle cx="7" cy="7" r="7" fill="var(--red)"/><path d="M3.5 7l2.5 2.5 4.5-5" fill="none" stroke="#fff" stroke-width="2"/></svg>GOODS</li>
  <li><svg width="14" height="14" viewBox="0 0 14 14"><circle cx="7" cy="7" r="7" fill="var(--red)"/><path d="M3.5 7l2.5 2.5 4.5-5" fill="none" stroke="#fff" stroke-width="2"/></svg>CHICOUTIMI</li>
</ul>
<ul class="abs off-list" style="left:385px;top:1949px">
  <li><svg width="14" height="14" viewBox="0 0 14 14"><circle cx="7" cy="7" r="7" fill="var(--red)"/><path d="M3.5 7l2.5 2.5 4.5-5" fill="none" stroke="#fff" stroke-width="2"/></svg>SEPT-ILES</li>
  <li><svg width="14" height="14" viewBox="0 0 14 14"><circle cx="7" cy="7" r="7" fill="var(--red)"/><path d="M3.5 7l2.5 2.5 4.5-5" fill="none" stroke="#fff" stroke-width="2"/></svg>ROUYN-NORANDA</li>
  <li><svg width="14" height="14" viewBox="0 0 14 14"><circle cx="7" cy="7" r="7" fill="var(--red)"/><path d="M3.5 7l2.5 2.5 4.5-5" fill="none" stroke="#fff" stroke-width="2"/></svg>VAL D'OR</li>
  <li><svg width="14" height="14" viewBox="0 0 14 14"><circle cx="7" cy="7" r="7" fill="var(--red)"/><path d="M3.5 7l2.5 2.5 4.5-5" fill="none" stroke="#fff" stroke-width="2"/></svg>GATINEAU</li>
  <li><svg width="14" height="14" viewBox="0 0 14 14"><circle cx="7" cy="7" r="7" fill="var(--red)"/><path d="M3.5 7l2.5 2.5 4.5-5" fill="none" stroke="#fff" stroke-width="2"/></svg>VICTORIAVILLE</li>
</ul>
<ul class="abs off-list" style="left:548px;top:1949px">
  <li><svg width="14" height="14" viewBox="0 0 14 14"><circle cx="7" cy="7" r="7" fill="var(--red)"/><path d="M3.5 7l2.5 2.5 4.5-5" fill="none" stroke="#fff" stroke-width="2"/></svg>AMQUI</li>
  <li><svg width="14" height="14" viewBox="0 0 14 14"><circle cx="7" cy="7" r="7" fill="var(--red)"/><path d="M3.5 7l2.5 2.5 4.5-5" fill="none" stroke="#fff" stroke-width="2"/></svg>WOLF RIVER</li>
  <li><svg width="14" height="14" viewBox="0 0 14 14"><circle cx="7" cy="7" r="7" fill="var(--red)"/><path d="M3.5 7l2.5 2.5 4.5-5" fill="none" stroke="#fff" stroke-width="2"/></svg>CHATEAUGUAY</li>
  <li><svg width="14" height="14" viewBox="0 0 14 14"><circle cx="7" cy="7" r="7" fill="var(--red)"/><path d="M3.5 7l2.5 2.5 4.5-5" fill="none" stroke="#fff" stroke-width="2"/></svg>LA PRAIRIE</li>
</ul>

<!-- footer -->
<footer class="abs footer"></footer>
<div class="abs footer-brand"><span class="brand-square"></span><span class="brand-name">Le Pont d'Oriole</span></div>
<div class="abs divider" style="left:245px"></div>
<div class="abs divider" style="left:510px"></div>
<div class="abs divider" style="left:835px"></div>

<div class="abs f-head" style="left:278px;top:2174px">Hours of Operation</div>
<table class="abs hours" style="left:278px;top:2214px;color:#ddd;border-collapse:collapse">
  <tr><td style="width:112px">Monday to Friday:</td><td>7am to 21hrs</td></tr>
  <tr><td>Sunday:</td><td>&nbsp;&nbsp;10hrs to 15hrs</td></tr>
</table>

<div class="abs f-head" style="left:541px;top:2174px">Newsletter</div>
<p class="abs f-text" style="left:541px;top:2208px;width:260px">Register your email address to get information ablout us</p>
<div class="abs news-input">Email Address</div>
<div class="abs news-btn">SUBSCRIBE</div>

<div class="abs f-head" style="left:865px;top:2174px">Contact Us</div>
<div class="abs contact-row" style="left:866px;top:2215px">
  <svg width="10" height="14" viewBox="0 0 10 14"><path d="M5 0a5 5 0 015 5c0 4-5 9-5 9S0 9 0 5a5 5 0 015-5z" fill="#ddd"/><circle cx="5" cy="5" r="2" fill="#262626"/></svg>48 Verdier Street, La Prairie, QC, J5R 0K4</div>
<div class="abs contact-row" style="left:866px;top:2265px">
  <svg width="12" height="12" viewBox="0 0 24 24"><path d="M6.6 10.8a15 15 0 006.6 6.6l2.2-2.2c.3-.3.7-.4 1-.2 1.1.4 2.3.6 3.6.6.6 0 1 .4 1 1V20c0 .6-.4 1-1 1A17 17 0 013 4c0-.6.4-1 1-1h3.5c.6 0 1 .4 1 1 0 1.3.2 2.5.6 3.6.1.3 0 .7-.2 1z" fill="#ddd"/></svg>1-855-555-0147</div>
<div class="abs contact-row" style="left:866px;top:2314px">
  <svg width="13" height="10" viewBox="0 0 14 11"><rect x="0.5" y="0.5" width="13" height="10" fill="#ddd"/><path d="M1 1l6 5 6-5" fill="none" stroke="#262626"/></svg>contact@lepontdoriole.ca</div>

<div class="abs bottom"></div>
<p class="abs copy">Copyrights ©2016, Le Pont d'Oriole. All rights reserved.</p>
<div class="abs social" aria-label="Social links"><span></span><span></span><span></span><span></span></div>

</body>
</html>
```